Book Cover for a Short Story called “Leaving Harbor"

Pretty Straightforward. Looking for a 5.5X8.5 book cover. The story is a very short (40 pages) story about a man who moves from Greece to Canada in 1920. I have three photos to provide. One is the house that he left in greece. THen I have photos of him and his wife who he met in Toronto. I think I want the house photo on the front...
I will need cover for paper back and e-book. The ISBN numbers are:

ISBN: 978-1-5523094-2-7 (e-book)
ISBN: 978-1-5523094-1-0 (paperback)

If you want you can read it at https://kevinmarlow.example/fiction/leaving-harbor/

Colors
0094D4
00A9DD
6FCCEA
C7EBF8
E9F6FB

Requirements
Must have
• Room for a blurb about the book on the back cover. ISBN Number

```html
<!DOCTYPE html>
<html lang="en">
<head>
<meta charset="utf-8">
<title>Leaving Harbor — Cover Spread</title>
<link href="https://fonts.googleapis.com/css2?family=EB+Garamond:wght@400;500&family=Mrs+Saint+Delafield&display=swap" rel="stylesheet">
<style>
  :root {
    --backdrop: #4a4a4a;
    --paper: #ffffff;
    --ink: #111111;
    --gold: #bf9a55;
    --photo-light: #e4e3e0;
    --photo-mid: #a9a8a4;
    --photo-dark: #5e5d5a;
    --portrait-navy: #2c3a5c;
    --portrait-skin: #d9a992;
  }
  * { margin: 0; padding: 0; box-sizing: border-box; }
  html, body {
    width: 1200px; height: 761px; overflow: hidden;
    background: var(--backdrop);
  }
  .spread {
    position: absolute; left: 150px; top: 34px;
    width: 900px; height: 694px;
    background: var(--paper);
    font-family: "EB Garamond", Georgia, serif;
    color: var(--ink);
  }
  /* Back cover */
  .back-title {
    position: absolute; left: 46px; top: 74px;
    font-size: 70px; font-weight: 400; line-height: 1;
    white-space: nowrap;
  }
  .back-title .script {
    font-family: "Mrs Saint Delafield", cursive;
    color: var(--gold); font-size: 52px; margin-left: 4px;
  }
  .blurb {
    position: absolute; font-size: 11.2px; line-height: 14.4px;
    text-align: justify;
  }
  .blurb-main { left: 46px; top: 162px; width: 365px; }
  .blurb-side { left: 206px; top: 339px; width: 204px; }
  .author-portrait {
    position: absolute; left: 9px; top: 311px; width: 238px; height: 302px;
    background:
      radial-gradient(ellipse 30% 24% at 48% 26%, var(--portrait-skin) 0%, rgba(217,169,146,0) 100%),
      radial-gradient(ellipse 70% 55% at 45% 70%, var(--portrait-navy) 0%, rgba(44,58,92,0.5) 60%, rgba(255,255,255,0) 100%);
  }
  .isbn {
    position: absolute; left: 31px; top: 637px;
    font-size: 9.5px;
  }
  /* Front cover */
  .front-photo {
    position: absolute; left: 454px; top: 0; width: 446px; height: 349px;
    background: linear-gradient(160deg, var(--photo-light) 0%, var(--photo-mid) 45%, var(--photo-dark) 75%, var(--photo-light) 100%);
  }
  .front-title {
    position: absolute; left: 454px; width: 446px; top: 415px;
    text-align: center; line-height: 1;
  }
  .front-title .main {
    display: block; font-size: 112px; font-weight: 400;
  }
  .front-title .script {
    display: block; margin: -22px 0 0 80px;
    font-family: "Mrs Saint Delafield", cursive;
    color: var(--gold); font-size: 78px;
  }
  .author-name {
    position: absolute; left: 454px; width: 446px; top: 628px;
    text-align: center; font-size: 19px; letter-spacing: 4.5px;
  }
</style>
</head>
<body>
  <main class="spread">
    <section class="back-cover">
      <h2 class="back-title">Leaving<span class="script">harbor</span></h2>
      <p class="blurb blurb-main">Lorem ipsum dolor sit amet, consectetur adipiscing elit, sed do eiusmod tempor incididunt ut labore et dolore magna aliqua. Quis ipsum suspendisse ultrices gravida. Risus commodo viverra maecenas accumsan lacus vel facilisis. Lorem ipsum dolor sit amet, consectetur adipiscing elit, sed do eiusmod tempor incididunt ut labore et dolore magna aliqua.<br>Quis ipsum suspendisse ultrices gravida. Risus commodo viverra maecenas accumsan lacus vel facilisis. Lorem ipsum dolor sit amet, consectetur adipiscing elit, sed do eiusmod tempor incididunt ut labore et dolore magna aliqua. Quis ipsum suspendisse ultrices gravida. Risus commodo viverra maecenas accumsan lacus vel facilisis.</p>
      <div class="author-portrait" role="img" aria-label="Portrait of the author in a navy blazer, arms crossed, fading into white"></div>
      <p class="blurb blurb-side">Quis ipsum suspendisse ultrices gravida. Risus commodo viverra maecenas accumsan lacus vel facilisis. Lorem ipsum dolor sit amet, consectetur adipiscing elit, sed do eiusmod tempor incididunt ut labore et dolore magna aliqua. Quis ipsum suspendisse ultrices gravida. Risus commodo viverra maecenas accumsan lacus vel facilisis.</p>
      <p class="isbn">ISBN: 978-1-5523094-1-0</p>
    </section>
    <section class="front-cover">
      <div class="front-photo" role="img" aria-label="Stack of old black-and-white photographs and letters showing a stone house in a Greek village"></div>
      <h1 class="front-title"><span class="main">Leaving</span><span class="script">harbor</span></h1>
      <p class="author-name">KEVIN MARLOW</p>
    </section>
  </main>
</body>
</html>
```